Business Card For Halvenmoor Financial Consulting

Hi, I would like a business card designed. Bold, modern.
Please use the same design as the logo. I have also attached the website design to see the overall theme.
Wordmark Font
Color: Hex: #01AEF7

```html
<!DOCTYPE html>
<html lang="en">
<head>
<meta charset="UTF-8">
<title>Halvenmoor Consulting – Business Card</title>
<link href="https://fonts.googleapis.com/css2?family=Montserrat:wght@600;700&family=Open+Sans:wght@400;600&display=swap" rel="stylesheet">
<style>
  :root {
    --bg: #e4e1dc;
    --card: #14202a;
    --card-tint: #182a38;
    --accent: #01aef7;
    --accent-soft: #2a9fd8;
    --white: #f2f4f6;
    --rule: #8796a3;
  }
  * { margin: 0; padding: 0; box-sizing: border-box; }
  html, body { width: 1200px; height: 900px; overflow: hidden; }
  body {
    background: var(--bg);
    font-family: "Open Sans", Arial, sans-serif;
    position: relative;
  }
  .card {
    position: absolute;
    left: 290px;
    width: 620px;
    height: 354px;
    background: var(--card);
    border-radius: 38px;
    overflow: hidden;
    box-shadow: 0 14px 30px rgba(0,0,0,0.28);
  }
  .card--front { top: 72px; }
  .card--back { top: 474px; }

  .brand {
    position: absolute;
    display: flex;
    align-items: center;
    gap: 14px;
  }
  .brand__mark {
    width: 40px;
    height: 40px;
    border: 4px solid var(--accent);
  }
  .brand__name {
    font-family: "Montserrat", Arial, sans-serif;
    font-weight: 700;
    color: var(--white);
    letter-spacing: 0.04em;
    text-transform: uppercase;
    line-height: 1;
  }
  .card--front .brand {
    left: 50%;
    top: 50%;
    transform: translate(-50%, -50%);
  }
  .card--front .brand__name { font-size: 30px; }

  .card--back .brand { left: 40px; top: 44px; }
  .card--back .brand__name { font-size: 26px; }
  .card--back .brand__mark { width: 36px; height: 36px; }

  .backdrop-panel {
    position: absolute;
    left: 60px;
    top: 120px;
    width: 260px;
    height: 260px;
    border: 14px solid var(--card-tint);
  }

  .person {
    position: absolute;
    right: 318px;
    top: 206px;
    text-align: right;
  }
  .person__role {
    font-size: 15px;
    color: var(--white);
    margin-bottom: 4px;
  }
  .person__name {
    font-family: "Montserrat", Arial, sans-serif;
    font-weight: 700;
    font-size: 21px;
    color: var(--accent-soft);
    text-transform: uppercase;
  }
  .divider {
    position: absolute;
    left: 318px;
    top: 178px;
    width: 1px;
    height: 120px;
    background: var(--rule);
  }
  .contact {
    position: absolute;
    left: 336px;
    top: 180px;
    list-style: none;
  }
  .contact__item {
    display: flex;
    align-items: flex-start;
    gap: 9px;
    font-size: 14px;
    color: var(--white);
    line-height: 1.45;
    margin-bottom: 3px;
  }
  .contact__icon { width: 14px; height: 14px; margin-top: 3px; flex: none; }
  .contact__icon path, .contact__icon circle { fill: var(--accent-soft); }
</style>
</head>
<body>

  <section class="card card--front">
    <div class="brand">
      <div class="brand__mark"></div>
      <span class="brand__name">Halvenmoor Consulting</span>
    </div>
  </section>

  <section class="card card--back">
    <div class="backdrop-panel"></div>

    <div class="brand">
      <div class="brand__mark"></div>
      <span class="brand__name">Halvenmoor Consulting</span>
    </div>

    <div class="person">
      <p class="person__role">Manager</p>
      <p class="person__name">Marcus Ellery</p>
    </div>

    <div class="divider"></div>

    <ul class="contact">
      <li class="contact__item">
        <svg class="contact__icon" viewBox="0 0 16 16"><path d="M3 1h3l1.5 4-2 1.2a9 9 0 0 0 4.3 4.3L11 8.5l4 1.5v3c0 1-1 2-2 2A12 12 0 0 1 1 3c0-1 1-2 2-2z"/></svg>
        (041) 582 30417
      </li>
      <li class="contact__item">
        <svg class="contact__icon" viewBox="0 0 16 16"><path d="M1 3h14v10H1zM2.5 4.5 8 9l5.5-4.5v-.2H2.5z"/></svg>
        info@halvenmoorconsulting.com
      </li>
      <li class="contact__item">
        <svg class="contact__icon" viewBox="0 0 16 16"><path d="M8 1a7 7 0 1 0 0 14A7 7 0 0 0 8 1zm0 1.5c.9 0 1.9 1.7 2.2 4.5H5.8C6.1 4.2 7.1 2.5 8 2.5zM2.6 7h1.8a11 11 0 0 1 .5-3.6A5.5 5.5 0 0 0 2.6 7zm8.9 0h1.9a5.5 5.5 0 0 0-2.3-3.6c.3 1 .4 2.3.4 3.6zM2.6 9a5.5 5.5 0 0 0 2.3 3.6A11 11 0 0 1 4.4 9zm3.2 0c.3 2.8 1.3 4.5 2.2 4.5s1.9-1.7 2.2-4.5zm5.7 0c0 1.3-.2 2.6-.5 3.6A5.5 5.5 0 0 0 13.4 9z"/></svg>
        www.halvenmoorconsulting.com
      </li>
      <li class="contact__item">
        <svg class="contact__icon" viewBox="0 0 16 16"><path d="M8 0a5.5 5.5 0 0 0-5.5 5.5C2.5 10 8 16 8 16s5.5-6 5.5-10.5A5.5 5.5 0 0 0 8 0zm0 8a2.5 2.5 0 1 1 0-5 2.5 2.5 0 0 1 0 5z"/></svg>
        <span>2816 Brambleton Road<br>Eastvale, OR 97310</span>
      </li>
    </ul>
  </section>

</body>
</html>
```